Boutique custom software development company needs new business card

Our nearly 20 year old custom software development company would like to better include the fact that we are now providing Bitcoin services. These new services are B2B include education (how to acquire and securely hold Bitcoin) and integrating Bitcoin payments into existing ecommerce sites or other existing systems. Please keep the card clean and simple. Attached is our current design and some other files. vextorial.com

Target Market(s)

businesses owners interested in long term relationship

Industry/Entity Type

Custom software development and Bitcoin

Contact Information for Business Card

Dale Parker, dale@vextorial.com, vextorial.com, (888) 555-VXTRL

Font styles to use
Other font styles liked:
• monospace

Requirements
Must have
• double-sided
Nice to have
• clean and simple
Should not have
• physical address

```html
<!DOCTYPE html>
<html lang="en">
<head>
<meta charset="utf-8">
<title>Vextorial — Business Card</title>
<link rel="stylesheet" href="https://fonts.googleapis.com/css2?family=Open+Sans:wght@400;700;800&display=swap">
<style>
  :root {
    --blue: #3b73b9;
    --blue-deep: #2f5f9c;
    --orange: #ee7d22;
    --white: #ffffff;
    --ink: #111111;
    --stage: #ababab;
  }
  * { box-sizing: border-box; margin: 0; padding: 0; }
  html, body { width: 1200px; height: 936px; overflow: hidden; }
  body {
    background: var(--stage);
    font-family: "Open Sans", Arial, sans-serif;
    position: relative;
  }
  .card {
    position: absolute;
    left: 320px;
    width: 560px;
    height: 320px;
    overflow: hidden;
    box-shadow: 0 6px 18px rgba(0,0,0,0.25);
  }
  .card--front { top: 90px; background: var(--white); }
  .card--back { top: 520px; background: var(--blue); }

  /* Front */
  .front-contact-panel {
    position: absolute;
    left: 0; top: 112px;
    width: 346px; height: 208px;
    background: var(--blue);
  }
  .front-corner-panel {
    position: absolute;
    right: 0; bottom: 0;
    width: 214px; height: 128px;
    background: var(--blue);
    clip-path: polygon(14% 0, 100% 0, 100% 100%, 0 100%);
  }
  .front-corner-block {
    position: absolute;
    right: 142px; bottom: 38px;
    width: 34px; height: 34px;
    background: var(--orange);
  }
  .front-tab {
    position: absolute;
    right: 0; top: 168px;
    width: 18px; height: 26px;
    background: var(--orange);
  }
  .brand {
    position: absolute;
    left: 32px; top: 26px;
  }
  .brand__name {
    font-weight: 800;
    font-size: 40px;
    line-height: 1;
    letter-spacing: -1px;
    color: var(--orange);
  }
  .brand__tagline {
    margin-top: 4px;
    font-size: 13px;
    letter-spacing: -0.3px;
    color: var(--blue);
  }
  .holder-name {
    position: absolute;
    right: 34px; top: 150px;
    font-weight: 800;
    font-size: 24px;
    letter-spacing: 0.5px;
  }
  .holder-name__first { color: var(--orange); }
  .holder-name__last { color: var(--blue); }
  .contact {
    position: absolute;
    left: 32px; top: 140px;
    list-style: none;
    color: var(--white);
    font-size: 13px;
    line-height: 20px;
  }
  .contact li { display: flex; align-items: center; gap: 7px; }
  .contact svg { width: 12px; height: 12px; flex: none; }
  .contact__service { padding-left: 19px; }

  /* Back */
  .back-brand {
    position: absolute;
    left: 0; right: 0; top: 104px;
    text-align: center;
  }
  .back-brand__name {
    font-weight: 800;
    font-size: 64px;
    line-height: 1;
    letter-spacing: -2px;
    color: var(--ink);
  }
  .back-brand__tagline {
    margin-top: 8px;
    font-size: 19px;
    letter-spacing: -0.4px;
    color: var(--ink);
  }
</style>
</head>
<body>

  <section class="card card--front" aria-label="Business card front">
    <div class="front-contact-panel"></div>
    <div class="front-corner-panel"></div>
    <div class="front-corner-block"></div>
    <div class="front-tab"></div>

    <div class="brand">
      <div class="brand__name">Vextorial</div>
      <div class="brand__tagline">developer of custom applications</div>
    </div>

    <div class="holder-name">
      <span class="holder-name__first">Dale</span>
      <span class="holder-name__last">Parker</span>
    </div>

    <ul class="contact">
      <li class="contact__service">Custom software development</li>
      <li class="contact__service">Bitcoin education &amp; payments</li>
      <li>
        <svg viewBox="0 0 24 24" aria-hidden="true"><path fill="#fff" d="M6.6 10.8a15 15 0 0 0 6.6 6.6l2.2-2.2a1 1 0 0 1 1-.25 11.4 11.4 0 0 0 3.6.57 1 1 0 0 1 1 1V20a1 1 0 0 1-1 1A17 17 0 0 1 3 4a1 1 0 0 1 1-1h3.5a1 1 0 0 1 1 1c0 1.25.2 2.45.57 3.57a1 1 0 0 1-.25 1z"/></svg>
        (888) 555-VXTRL
      </li>
      <li>
        <svg viewBox="0 0 24 24" aria-hidden="true"><circle cx="12" cy="12" r="9.5" fill="none" stroke="#fff" stroke-width="2"/><path d="M2.5 12h19M12 2.5c3 3 3 16 0 19M12 2.5c-3 3-3 16 0 19" fill="none" stroke="#fff" stroke-width="1.6"/></svg>
        www.vextorial.com
      </li>
      <li>
        <svg viewBox="0 0 24 24" aria-hidden="true"><rect x="2" y="5" width="20" height="14" rx="1.5" fill="none" stroke="#fff" stroke-width="2"/><path d="M2.5 6l9.5 7 9.5-7" fill="none" stroke="#fff" stroke-width="2"/></svg>
        dale@vextorial.com
      </li>
    </ul>
  </section>

  <section class="card card--back" aria-label="Business card back">
    <div class="back-brand">
      <div class="back-brand__name">Vextorial</div>
      <div class="back-brand__tagline">developer of custom applications</div>
    </div>
  </section>

</body>
</html>
```